Boutique town planning business needs a Business Card design

We need a business card design for a new company called The Zoning Bridgeway. We provide town planning and urban design services to government, business and community groups. We would like to see the designs use the colours in the logo (blue, deep red, green and amber), plenty of white and including black and grey in the writing. The final design should communicate collaboration, creativity and professionalism and that we are approachable.

Industry/Entity Type

Town

```html
<!DOCTYPE html>
<html lang="en">
<head>
<meta charset="utf-8">
<title>The Zoning Bridgeway — Business Card</title>
<link href="https://fonts.googleapis.com/css2?family=Open+Sans:wght@400;600&family=Oswald:wght@500&display=swap" rel="stylesheet">
<style>
  :root {
    --backdrop: #e8e6e2;
    --card-white: #ffffff;
    --card-grey: #e4e4e4;
    --band-dark: #2e2e30;
    --band-black: #111112;
    --text-dark: #2a2a2a;
    --text-grey: #6b6b6b;
    --accent-amber: #f28c1c;
    --mark-blue: #1f9ad6;
  }
  * { box-sizing: border-box; margin: 0; padding: 0; }
  html, body {
    width: 1057px; height: 1200px; overflow: hidden;
    background: var(--backdrop);
    font-family: "Open Sans", Arial, sans-serif;
  }
  .card {
    position: absolute; left: 98px; width: 860px; height: 490px;
    background: radial-gradient(ellipse at 40% 40%, var(--card-white) 35%, var(--card-grey) 100%);
    box-shadow: 0 10px 30px rgba(0,0,0,0.18);
    overflow: hidden;
  }
  .card--front { top: 70px; }
  .card--back { top: 640px; }

  .brand { position: absolute; display: flex; align-items: center; gap: 18px; }
  .brand__dot { width: 74px; height: 74px; border-radius: 50%; background: var(--mark-blue); flex: none; }
  .brand__name { font-weight: 600; color: var(--text-dark); line-height: 1.05; white-space: nowrap; }
  .card--front .brand { left: 250px; top: 150px; }
  .card--front .brand__name { font-size: 34px; }

  .band { position: absolute; left: 0; right: 0; display: flex; align-items: center; justify-content: center; color: #fff; letter-spacing: 4px; }
  .band--front { top: 360px; height: 54px; background: var(--band-dark); font-size: 17px; }
  .band--back { top: 385px; height: 56px; background: var(--band-black); font-size: 18px; letter-spacing: 2px; }

  .accent-line { position: absolute; height: 5px; background: var(--accent-amber); }
  .accent-line--top { left: 0; top: 120px; width: 300px; }
  .accent-line--bottom { left: 330px; top: 340px; width: 530px; }
  .accent-line--side { left: 320px; top: 120px; width: 5px; height: 225px; }

  .person { position: absolute; left: 345px; top: 50px; }
  .person__name { font-family: "Oswald", "Arial Narrow", sans-serif; font-weight: 500; font-size: 44px; letter-spacing: 1px; color: var(--text-dark); line-height: 1; }
  .person__role { font-size: 17px; letter-spacing: 2px; color: var(--text-grey); margin-top: 6px; }

  .contacts { position: absolute; left: 345px; top: 170px; list-style: none; }
  .contacts li { display: flex; align-items: center; gap: 14px; height: 38px; font-size: 16px; color: var(--text-grey); }
  .contacts svg { width: 26px; height: 26px; flex: none; }

  .card--back .brand { left: 36px; top: 205px; gap: 12px; }
  .card--back .brand__dot { width: 50px; height: 50px; }
  .card--back .brand__name { font-size: 20px; }
</style>
</head>
<body>
  <section class="card card--front" aria-label="Card front">
    <div class="brand">
      <span class="brand__dot"></span>
      <span class="brand__name">The<br>Zoning Bridgeway</span>
    </div>
    <div class="band band--front">www.zoningbridgeway.com</div>
  </section>

  <section class="card card--back" aria-label="Card back">
    <span class="accent-line accent-line--top"></span>
    <span class="accent-line accent-line--side"></span>
    <span class="accent-line accent-line--bottom"></span>

    <div class="person">
      <p class="person__name">CLARA WESTON</p>
      <p class="person__role">GENERAL MANAGER</p>
    </div>

    <ul class="contacts">
      <li>
        <svg viewBox="0 0 26 26" aria-hidden="true"><rect width="26" height="26" rx="3" fill="#f28c1c"/><path d="M8 6h3l1.5 4-2 1.5a9 9 0 0 0 4 4l1.5-2 4 1.5v3a2 2 0 0 1-2 2A13 13 0 0 1 6 8a2 2 0 0 1 2-2z" fill="#fff"/></svg>
        014 552 3190
      </li>
      <li>
        <svg viewBox="0 0 26 26" aria-hidden="true"><rect width="26" height="26" rx="3" fill="#f28c1c"/><rect x="6" y="7" width="14" height="12" rx="1" fill="none" stroke="#fff" stroke-width="2"/><path d="M10 16h6M10 12h6" stroke="#fff" stroke-width="1.6"/></svg>
        014 552 3191
      </li>
      <li>
        <svg viewBox="0 0 26 26" aria-hidden="true"><rect width="26" height="26" rx="3" fill="#f28c1c"/><rect x="5" y="8" width="16" height="11" fill="none" stroke="#fff" stroke-width="2"/><path d="M5 8l8 6 8-6" fill="none" stroke="#fff" stroke-width="2"/></svg>
        clara@zoningbridgeway.com
      </li>
      <li>
        <svg viewBox="0 0 26 26" aria-hidden="true"><rect width="26" height="26" rx="3" fill="#f28c1c"/><circle cx="13" cy="13" r="7" fill="none" stroke="#fff" stroke-width="2"/><path d="M6 13h14M13 6c-3 4-3 10 0 14M13 6c3 4 3 10 0 14" fill="none" stroke="#fff" stroke-width="1.5"/></svg>
        www.zoningbridgeway.com
      </li>
    </ul>

    <div class="brand">
      <span class="brand__dot"></span>
      <span class="brand__name">The<br>Zoning Bridgeway</span>
    </div>

    <div class="band band--back">27 Alder Lane, 2nd Floor, North Quarter</div>
  </section>
</body>
</html>
```